Web Design Project

Psychotherapy and Counselling Practice needs a landing page web design.

My business "Larkfield Advisory" specialises in the treatment of Anxiety and Depression with a holistic approach, endeavouring to unlock the key that holds us to ransom in a life that is imbalanced, frustrating, and ultimately of our own making due to our own perceptions and behaviours.

There is much that impacts us which we cannot change, but we are always in control of how we think, and how we frame our experiences.....learning to challenge those thoughts and behaviours that are destructive and disempowering opens up a world of joyful possibility. Life is about making choices, learn to make wiser and healthier choices.......

Larkfield Advisory has a client base of individual clients but will seek to expand to offer services to the Corporate world by offering an adjunct to employers for established "Wellness Programs".

Larkfield Advisory is a highly professional, ethically bound business, with the needs of the client at the forefront of all we do.

Larkfield Advisory wishes to avoid the usual "jargon driven" psychobabble offered on many counselling web pages. It aims to be stylishly presented, clean in look and with as few "words" as possible and a largely white background (faster loading and more powerful impact of what is stated), those words contained in the webpage should be meaningful, persuasive and have an impact simply at glance. Larkfield does not want , or expect, those prospective clients in need of support , to be reading through volumes of industry driven cliches.

At this point Larkfield is just looking for a high quality landing page. However in time this will likely expand to include other sections such as case studies, video content etc.

Target Market(s)

Those in need of emotional support, suffering mental health issues, and those simply wanting to become self aware supported by a mindful therapist.

Industry/Entity Type

Industry

Requirements
Must have
• The design must incorporate the Larkfield logo and colour schemes found on the attached files.

```html
<!DOCTYPE html>
<html lang="en">
<head>
<meta charset="utf-8">
<title>Larkfield Advisory</title>
<link href="https://fonts.googleapis.com/css2?family=Pathway+Gothic+One&family=Questrial&family=Ubuntu:wght@400;500&family=Open+Sans:wght@400;600;700&display=swap" rel="stylesheet">
<style>
  :root {
    --green: #8aab0e;
    --grey: #707070;
    --grey-light: #9a9a9a;
    --rule: #f4f1dc;
    --white: #ffffff;
    --icon-dark: #333333;
  }
  * { margin: 0; padding: 0; box-sizing: border-box; }
  html, body { width: 1200px; height: 1000px; overflow: hidden; background: var(--white); }
  .page { position: relative; width: 1200px; height: 1000px; font-family: "Open Sans", sans-serif; }

  .main-nav { position: absolute; top: 35px; left: 138px; display: flex; align-items: center; }
  .main-nav a {
    font-family: "Questrial", sans-serif; font-size: 14px; color: var(--green);
    text-decoration: none; text-transform: uppercase; padding: 4px 12px; margin-right: 14px;
    border-radius: 4px; line-height: 20px; white-space: nowrap;
  }
  .main-nav a.is-active { background: var(--green); color: var(--white); }

  .search {
    position: absolute; top: 32px; left: 850px; width: 210px; height: 29px;
    border: 1px solid #e2e2e2; border-radius: 5px; display: flex; align-items: center;
    font-family: Arial, sans-serif; font-size: 12px; color: #222;
  }
  .search svg { margin: 0 8px 0 11px; }
  .search .clear { position: absolute; right: 5px; top: 4px; margin: 0; }

  .vine {
    position: absolute; left: 262px; top: 120px; width: 86px; height: 547px;
    background: linear-gradient(180deg, rgba(138,171,14,0.05), rgba(138,171,14,0.35) 50%, rgba(138,171,14,0.55));
    border-radius: 40px 40px 0 0;
  }
  .brand {
    position: absolute; left: 136px; top: 284px; width: 390px; white-space: nowrap;
    font-family: "Questrial", sans-serif; font-size: 72px; letter-spacing: 2px;
    color: var(--grey); line-height: 84px;
  }

  .quote {
    position: absolute; left: 540px; top: 144px; width: 525px; text-align: center;
    font-family: "Pathway Gothic One", sans-serif; font-size: 52px; line-height: 63px;
    color: var(--grey); text-transform: uppercase;
  }
  .quote span { display: block; white-space: nowrap; }
  .quote em { font-style: normal; color: var(--green); }
  .quote-author { position: absolute; left: 764px; top: 326px; width: 196px; height: 56px; }
  .quote-author svg { position: absolute; left: 0; top: 0; }
  .quote-author span {
    position: absolute; left: 0; top: 16px; width: 195px; height: 39px;
    font-family: "Pathway Gothic One", sans-serif; font-size: 19px; letter-spacing: 0.5px;
    color: var(--white); text-transform: uppercase; display: flex; align-items: center; justify-content: center;
  }

  .pitch {
    position: absolute; left: 616px; top: 436px; width: 410px; text-align: center; white-space: nowrap;
    font-family: "Ubuntu", sans-serif; font-size: 23px; color: var(--grey); letter-spacing: 0.5px;
  }
  .pitch strong { color: var(--green); font-weight: 500; }

  .contact-card {
    position: absolute; left: 616px; top: 482px; width: 410px; height: 163px;
    border-top: 1px solid var(--rule); border-bottom: 1px solid var(--rule); text-align: center;
  }
  .contact-card .call { font-family: "Ubuntu", sans-serif; font-size: 18px; color: var(--green); margin-top: 10px; }
  .contact-card .name { font-size: 24px; font-weight: 700; color: var(--grey); margin-top: 16px; line-height: 30px; }
  .contact-card .creds { font-size: 11px; color: var(--grey-light); line-height: 14px; }
  .contact-card .lines { margin-top: 16px; }
  .contact-card .line { font-size: 14px; font-weight: 600; color: var(--grey); line-height: 22px; }
  .contact-card .line a { color: var(--green); text-decoration: none; }

  .footer-band { position: absolute; left: 0; top: 667px; width: 1200px; height: 20px; background: var(--green); }
  .site-footer { position: absolute; left: 0; top: 687px; width: 1200px; height: 88px; background: var(--grey); }
  .social { position: absolute; left: 138px; top: 12px; display: flex; gap: 14px; }
  .social span {
    width: 34px; height: 34px; border-radius: 50%; background: var(--icon-dark);
    box-shadow: inset 0 0 0 2px #555;
  }
  .copyright { position: absolute; left: 138px; top: 60px; font-size: 11px; font-weight: 600; color: var(--white); letter-spacing: 0.3px; }
  .site-url { position: absolute; left: 662px; top: 20px; font-family: "Ubuntu", sans-serif; font-size: 26px; color: var(--green); white-space: nowrap; }
  .site-url small { font-size: 18px; }
</style>
</head>
<body>
<div class="page">
  <nav class="main-nav">
    <a href="#" class="is-active">Home</a>
    <a href="#">Our Services</a>
    <a href="#">Case Study</a>
    <a href="#">Who We Are</a>
    <a href="#">Contact Us</a>
  </nav>

  <div class="search">
    <svg width="16" height="16" viewBox="0 0 16 16"><circle cx="6.5" cy="6.5" r="4.5" fill="none" stroke="#333" stroke-width="1.8"/><line x1="10" y1="10" x2="14.5" y2="14.5" stroke="#333" stroke-width="2.4" stroke-linecap="round"/></svg>
    Search...
    <svg class="clear" width="20" height="20" viewBox="0 0 20 20"><circle cx="10" cy="10" r="10" fill="#8c8c8c"/><path d="M7 7 L13 13 M13 7 L7 13" stroke="#fff" stroke-width="2"/></svg>
  </div>

  <div class="vine" role="img" aria-label="Climbing green vine illustration rising through the brand name"></div>
  <div class="brand">LARKFIELD</div>

  <p class="quote">
    <span>Just <em>living</em> is not enough. One</span>
    <span><em>must have sunshine, freedom,</em></span>
    <span>and <em>a little flower</em>.</span>
  </p>
  <div class="quote-author">
    <svg width="196" height="56" viewBox="0 0 196 56"><path d="M20 0 L40 16 L190 16 Q195 16 195 21 L195 50 Q195 55 190 55 L6 55 Q1 55 1 50 L1 21 Q1 16 6 16 L20 16 Z" fill="#8aab0e"/></svg>
    <span>Elias Marwood</span>
  </div>

  <p class="pitch"><strong>Consulting</strong> is highly Professional</p>

  <div class="contact-card">
    <p class="call">Call Us Today:</p>
    <p class="name">MARA ELLISON</p>
    <p class="creds">BA (Psych) BSc (Hons) Psych MBPS</p>
    <div class="lines">
      <p class="line">Mobile: <a href="#">0400 128 736</a></p>
      <p class="line">E-mail: <a href="#">mara.ellison@larkmail.net</a></p>
    </div>
  </div>

  <div class="footer-band"></div>
  <footer class="site-footer">
    <div class="social" aria-label="Social links">
      <span></span><span></span><span></span><span></span>
    </div>
    <p class="copyright">Copyright © 2013 LARKFIELD - All rights reserved</p>
    <p class="site-url"><small>www.</small>larkfieldadvisory<small>.com.au</small></p>
  </footer>
</div>
</body>
</html>
```